International business needs business cards

Our company, DRV Ventures Inc. is in the business of supplying a range construction products with particular emphasis on CEMENT. We have developed our own brand - TORVAN SUPPLIES - with which to infiltrate the market. We are launching our brand of cement (TORVAN Type IS Cement) into the Caribbean which is unlike anything this market has ever seen. A monopoly has existed here for the past 60-odd years and the market has now opened to allow the importation of other brands and consumers are anxious and ready for change/improvement. We are very excited to be launching and want to make a great first impression. We will be conducting workshops and seminars (from government level to the hardware store owners) and we want our business card to give us the strong, confident introduction that we need.

Target Market(s)

construction; builders; engineers; home owners

Industry/Entity Type

Construction

Contact Information for Business Card

Marisol Depree
CEO
cell # 1 555 4180736
Ground floor,Lindell Plaza Suite 2734
George Town,Grand Cayman
Cayman Islands,KY1-4823
EMAIL: m.depree@drvventuresinc.example
web site drvventuresinc.example

COMPANY: skype info drv.ventures.example

second card
Yvette Brannock-Depree
CFO
CELL# 1 555 607 3941
George Town,Grand Cayman
Cayman Islands,KY1-4823
EMAIL: y.brannockdepree@drvventuresinc.example
website drvventuresinc.example

Requirements
Must have
• Business cards must display BOTH logos - DRV is the company and TORVAN is the brand.

```html
<!DOCTYPE html>
<html lang="en">
<head>
<meta charset="utf-8">
<title>DRV Ventures Inc. – Business Card</title>
<link rel="stylesheet" href="https://fonts.googleapis.com/css2?family=Open+Sans:wght@400;600;700&display=swap">
<style>
  :root {
    --backdrop: #3a3a3a;
    --card: #050505;
    --ink: #ffffff;
    --ink-soft: #d8d8d8;
    --crest: #8a8a8a;
    --crest-dark: #4a4a4a;
    --brand-red: #8e1c20;
  }
  * { margin: 0; padding: 0; box-sizing: border-box; }
  html, body { width: 1200px; height: 900px; overflow: hidden; }
  body {
    background: var(--backdrop);
    font-family: "Open Sans", Arial, sans-serif;
    color: var(--ink);
    position: relative;
  }
  .card {
    position: absolute;
    width: 640px;
    height: 366px;
    background: var(--card);
    box-shadow: 0 10px 30px rgba(0,0,0,.45);
    overflow: hidden;
  }
  .card-front { left: 200px; top: 60px; }
  .card-back  { left: 360px; top: 474px; }

  /* front */
  .brand-mark {
    position: absolute;
    left: 0; right: 0; top: 78px;
    display: flex; flex-direction: column; align-items: center; gap: 14px;
  }
  .brand-mark .brand-circle {
    width: 118px; height: 118px; border-radius: 50%;
    background: radial-gradient(circle at 50% 40%, var(--crest), var(--crest-dark));
  }
  .brand-mark .brand-name {
    font-weight: 600; font-size: 22px; letter-spacing: 6px; color: var(--crest);
  }
  .company-handle {
    position: absolute; left: 0; right: 0; top: 290px;
    display: flex; justify-content: center; align-items: center; gap: 8px;
    font-size: 15px; color: var(--ink);
  }
  .company-handle .handle-dot {
    width: 13px; height: 13px; border-radius: 50%; background: var(--ink);
  }

  /* back */
  .company-mark {
    position: absolute; left: 36px; top: 92px;
    display: flex; align-items: center; gap: 12px;
  }
  .company-mark .mark-square { width: 96px; height: 84px; background: var(--brand-red); flex: none; }
  .company-mark .company-name {
    font-weight: 700; font-size: 24px; line-height: 1.1; color: var(--ink);
  }
  .company-mark .company-name span { display: block; white-space: nowrap; }

  .holder {
    position: absolute; right: 40px; top: 92px; width: 250px; text-align: right;
  }
  .holder .holder-name {
    font-weight: 700; font-size: 22px; letter-spacing: .5px; text-transform: uppercase;
    white-space: nowrap;
    padding-bottom: 4px; border-bottom: 1px solid var(--ink-soft);
  }
  .holder .holder-title { font-size: 11px; color: var(--ink-soft); margin-top: 2px; }

  .contact {
    position: absolute; left: 150px; right: 40px; top: 212px;
    border-top: 1px solid var(--ink-soft);
    padding-top: 12px;
    font-size: 13.5px; font-weight: 600; line-height: 18px;
  }
  .contact .line { display: flex; align-items: center; gap: 6px; white-space: nowrap; }
  .contact svg { width: 11px; height: 11px; fill: none; stroke: var(--ink); stroke-width: 1.6; flex: none; }
</style>
</head>
<body>

  <section class="card card-front" aria-label="Business card front">
    <div class="brand-mark">
      <div class="brand-circle" aria-hidden="true"></div>
      <div class="brand-name">TORVAN</div>
    </div>
    <div class="company-handle">
      <span class="handle-dot" aria-hidden="true"></span>
      <span>drv.ventures.example</span>
    </div>
  </section>

  <section class="card card-back" aria-label="Business card back">
    <div class="company-mark">
      <div class="mark-square" aria-hidden="true"></div>
      <div class="company-name"><span>DRV Ventures</span><span>Inc.</span></div>
    </div>

    <div class="holder">
      <div class="holder-name">Marisol Depree</div>
      <div class="holder-title">CEO</div>
    </div>

    <div class="contact">
      <div class="line">Ground floor,Lindell Plaza Suite 2734</div>
      <div class="line">George Town,Grand Cayman</div>
      <div class="line">Cayman Islands,KY1-4823</div>
      <div class="line">
        <svg viewBox="0 0 12 12" aria-hidden="true"><path d="M2 1.5 L4.2 1.5 L5 4 L3.8 5 Q5 7.5 7 8.2 L8 7 L10.5 7.8 L10.5 10 Q5 10.5 1.5 3.5 Z"/></svg>
        <span>1 555 4180736</span>
      </div>
      <div class="line">
        <svg viewBox="0 0 12 12" aria-hidden="true"><rect x="1" y="2.5" width="10" height="7"/><path d="M1 2.5 L6 6.5 L11 2.5"/></svg>
        <span>m.depree@drvventuresinc.example</span>
      </div>
      <div class="line">
        <svg viewBox="0 0 12 12" aria-hidden="true"><circle cx="6" cy="6" r="4.8"/><path d="M1.2 6 H10.8 M6 1.2 Q3 6 6 10.8 M6 1.2 Q9 6 6 10.8"/></svg>
        <span>www.drvventuresinc.example</span>
      </div>
    </div>
  </section>

</body>
</html>
```